Tidewell Homecare

I am looking to have a website designed for a housekeeping company that looks similar to this one. https://marloweshomecare.example/

I need 5 websites designed but will start with this one to see how I like it.

Industry/Entity Type

House Cleaning

Coding

Coded - Design and coding required

Number of Pages Required

5+ page

Font styles to use
Serif
Script

Colors
ffffff
fdf9cf
fbf289
fbee3f
d6edf3
86cae7
33a6d7
edf1f8
cedeed

```html
<!DOCTYPE html>
<html lang="en">
<head>
<meta charset="utf-8">
<title>Tidewell Homecare</title>
<link href="https://fonts.googleapis.com/css2?family=Arimo:ital,wght@0,400;0,700;1,400;1,700&display=swap" rel="stylesheet">
<style>
:root{
  --white:#ffffff;
  --yellow:#fbee3f;
  --blue:#33a6d7;
  --ink:#1f1f1f;
  --text:#6b6b6b;
  --charcoal:#3b3b3b;
  --mist:#f1f1f2;
  --field-line:#cfcfcf;
}
*{box-sizing:border-box;margin:0;padding:0}
html,body{width:1200px;height:3789px;overflow:hidden}
body{position:relative;background:var(--white);font-family:"Arimo",Arial,sans-serif;color:var(--ink)}
.abs{position:absolute}

/* hero */
.hero{left:0;top:0;width:1200px;height:634px;background:linear-gradient(180deg,#7c8690 0%,#a5acb1 35%,#8e8a84 65%,#6e5a45 100%)}
.hero-window{left:620px;top:40px;width:580px;height:360px;background:linear-gradient(180deg,#c9cfd4,#9aa3aa);opacity:.55}
.brand{left:112px;top:30px;display:flex;align-items:center;gap:10px}
.brand-dot{width:54px;height:54px;border:2px solid var(--white);border-radius:50%}
.brand-name{font-weight:700;font-size:14px;color:var(--yellow);line-height:18px;width:110px;text-transform:uppercase}
.nav{top:42px;display:flex;font-size:14px;font-weight:700;color:var(--white);text-transform:uppercase}
.nav a{position:absolute;white-space:nowrap;color:inherit;text-decoration:none}
.nav .active{color:var(--yellow)}
.nav .active::after{content:"";position:absolute;left:0;right:0;top:24px;height:3px;background:var(--yellow)}
.cta{left:912px;top:25px;width:176px;height:53px;border-radius:27px;background:var(--yellow);font-weight:700;font-size:14px;display:flex;align-items:center;justify-content:center;color:var(--ink)}
.hero-title{left:112px;top:228px;font-size:51px;line-height:52px;font-weight:700;color:var(--white);text-transform:uppercase}
.hero-arrow{width:44px;height:44px;top:326px}
.scroll-down{left:567px;top:601px;width:66px;height:66px}

/* about */
.about-photo{left:112px;top:765px;width:488px;height:439px;background:linear-gradient(135deg,#e9e6e1,#c8cdc9 55%,#8a9c86)}
.card{background:var(--white);box-shadow:0 0 12px rgba(0,0,0,.12)}
.about-card{left:475px;top:765px;width:613px;height:316px;padding:40px 26px 0 50px}
.eyebrow{font-size:13px;color:var(--blue);text-transform:uppercase;margin-bottom:11px}
.heading{font-size:35px;font-weight:700;text-transform:uppercase;color:var(--ink);margin-bottom:18px}
.body{font-size:13.4px;line-height:25.6px;color:var(--text);text-align:justify}
.quote-box{left:615px;top:1096px;width:473px;height:108px;background:var(--yellow);text-align:center;padding-top:24px}
.quote-box small{display:block;font-size:13px;font-weight:700;text-transform:uppercase}
.quote-box strong{display:block;font-size:30px;margin-top:8px}

/* services */
.service{top:1307px;height:471px;width:600px;color:var(--white);text-align:center}
.service.residential{left:0;width:598px;background:linear-gradient(135deg,#45b1dd,var(--blue))}
.service.commercial{left:598px;width:602px;background:linear-gradient(135deg,#4a4a4a,var(--charcoal))}
.service-icon{width:126px;height:126px;border-radius:50%;background:var(--white);margin:80px auto 0;display:flex;align-items:center;justify-content:center}
.service h2{font-size:26px;margin-top:30px;text-transform:uppercase}
.service p{font-size:13.4px;line-height:25.6px;width:450px;margin:10px auto 0}

/* reliability */
.house-fade{left:0;top:2140px;width:470px;height:200px;background:linear-gradient(90deg,rgba(225,229,233,.6),rgba(255,255,255,0))}
.blue-frame{left:584px;top:1863px;width:488px;height:450px;background:var(--blue)}
.team-photo{left:601px;top:1881px;width:487px;height:440px;background:linear-gradient(135deg,#d7d4d0,#b9a897 50%,#2f4c3c)}
.reliability-card{left:113px;top:1943px;width:612px;height:316px;padding:40px 50px 0 27px}

/* estimate */
.estimate{left:0;top:2424px;width:1200px;height:432px;background:var(--mist)}
.section-title{width:1200px;left:0;text-align:center;font-size:35px;font-weight:700;text-transform:uppercase}
.field{height:50px;border:1px solid var(--field-line);background:var(--white);font-size:13.4px;color:var(--text);padding:17px 15px}
.submit{left:472px;top:2706px;width:237px;height:47px;background:var(--blue);color:var(--white);font-weight:700;font-size:13.4px;display:flex;align-items:center;justify-content:center}

/* vendors */
.vendor{width:188px;height:188px;border-radius:50%;top:3028px;background:radial-gradient(circle at 50% 40%,#5a6b7a,#2d3640);display:flex;align-items:center;justify-content:center}
.vendor span{width:60px;height:60px;border:3px solid var(--white);border-radius:8px}

/* testimonial */
.testimonial{left:0;top:3319px;width:1200px;height:391px;background:linear-gradient(90deg,#dfe3df 0%,#c7cfc4 40%,#c9a860 65%,#a24a4a 100%)}
.quote{left:113px;top:3399px;width:441px;font-size:14px;line-height:25.6px;font-style:italic;font-weight:700;color:var(--white);text-align:justify}
.quote cite{display:block;font-size:16px;margin-top:2px}
.slide-btn{width:52px;height:52px;border-radius:50%;top:3570px;display:flex;align-items:center;justify-content:center}

/* footer */
.footer{left:0;top:3710px;width:1200px;height:79px;background:var(--white)}
.social{width:34px;height:34px;border-radius:50%;background:var(--blue);top:3730px}
.copyright{right:88px;top:3739px;font-size:13.4px;color:var(--charcoal)}
</style>
</head>
<body>

<!-- Hero -->
<div class="abs hero" role="img" aria-label="Bright seaside living room with striped armchairs and ocean view windows"></div>
<div class="abs hero-window"></div>
<div class="abs brand"><span class="brand-dot"></span><span class="brand-name">Tidewell Homecare</span></div>
<nav class="abs nav" style="left:0">
  <a class="active" style="left:363px">Home</a>
  <a style="left:443px">Services</a>
  <a style="left:553px">Gift Cards</a>
  <a style="left:678px">About</a>
  <a style="left:766px">Contact</a>
</nav>
<div class="abs cta">FREE ESTIMATE</div>
<h1 class="abs hero-title">The Importance<br>of Good<br>Housekeeping</h1>
<svg class="abs hero-arrow" style="left:34px" viewBox="0 0 44 44"><circle cx="22" cy="22" r="20" fill="none" stroke="#fff" stroke-width="2"/><path d="M25 14 17 22l8 8" fill="none" stroke="#fff" stroke-width="2"/></svg>
<svg class="abs hero-arrow" style="left:1122px" viewBox="0 0 44 44"><circle cx="22" cy="22" r="20" fill="none" stroke="#fff" stroke-width="2"/><path d="M19 14l8 8-8 8" fill="none" stroke="#fff" stroke-width="2"/></svg>
<svg class="abs scroll-down" viewBox="0 0 66 66"><circle cx="33" cy="33" r="32" fill="#fff"/><circle cx="33" cy="33" r="26" fill="none" stroke="#333" stroke-width="2"/><path d="M33 22v18M26 33l7 8 7-8" fill="none" stroke="#111" stroke-width="3"/></svg>

<!-- About -->
<div class="abs about-photo" role="img" aria-label="Housekeepers in green aprons and yellow gloves dusting and cleaning a table"></div>
<div class="abs card about-card">
  <p class="eyebrow">The Best Cleaning Company</p>
  <h2 class="heading">About Tidewell Homecare</h2>
  <p class="body">Lorem ipsum dolor sit amet, consectetur adipiscing elit, sed do eiusmod tempor incididunt ut labore et dolore magna aliqua. Ut enim ad minim veniam, quis nostrud exercitation ullamco laboris nisi ut aliquip ex ea commodo consequ at.Lorem ipsum dolor sit amet, consectetur adipiscing elit, sed do eiusmod tempor incididunt ut labore et dolore magna aliqua. Ut enim ad minim veniam, quis nostrud exercitation ullamco laboris nisi ut aliquip ex ea commodo consequat.</p>
</div>
<div class="abs quote-box"><small>Get a free quote today</small><strong>+1 888 888 8888</strong></div>

<!-- Services -->
<div class="abs service residential">
  <div class="service-icon"><svg width="66" height="60" viewBox="0 0 66 60" fill="none" stroke="#666" stroke-width="2.5"><path d="M4 30 33 5l29 25M12 24v32h42V24M26 56V38h14v18"/></svg></div>
  <h2>Residential Cleaning</h2>
  <p>Lorem ipsum dolor sit amet, consectetur adipiscing elit, sed do eiusmod tempor incididunt ut labore et dolore magna aliqua. Ut enim ad minim veniam, quis nostrud exercitation ullamco laboris nisi ut aliquip ex ea commodo consequat.</p>
</div>
<div class="abs service commercial">
  <div class="service-icon"><svg width="70" height="70" viewBox="0 0 70 70" fill="none" stroke="#666" stroke-width="2"><path d="M22 64V8h26v56M6 64h58M12 64V40h10M48 40h10v24"/><path d="M28 16h4M38 16h4M28 26h4M38 26h4M28 36h4M38 36h4M28 46h4M38 46h4M31 64v-8h8v8"/></svg></div>
  <h2>Commercial/Office Cleaning</h2>
  <p>Lorem ipsum dolor sit amet, consectetur adipiscing elit, sed do eiusmod tempor incididunt ut labore et dolore magna aliqua. Ut enim ad minim veniam, quis nostrud exercitation ullamco laboris nisi ut aliquip ex ea commodo consequat.</p>
</div>

<!-- Reliability -->
<div class="abs house-fade" role="img" aria-label="Faint sketch of a house"></div>
<div class="abs blue-frame"></div>
<div class="abs team-photo" role="img" aria-label="Smiling cleaning team in green aprons with yellow gloves"></div>
<div class="abs card reliability-card">
  <p class="eyebrow">The Best Cleaning Company</p>
  <h2 class="heading">Hard Work &amp; Reliability</h2>
  <p class="body">Lorem ipsum dolor sit amet, consectetur adipiscing elit, sed do eiusmod tempor incididunt ut labore et dolore magna aliqua. Ut enim ad minim veniam, quis nostrud exercitation ullamco laboris nisi ut aliquip ex ea commodo consequ at.Lorem ipsum dolor sit amet, consectetur adipiscing elit, sed do eiusmod tempor incididunt ut labore et dolore magna aliqua. Ut enim ad minim veniam, quis nostrud exercitation ullamco laboris nisi ut aliquip ex ea commodo consequat.</p>
</div>

<!-- Estimate form -->
<div class="abs estimate"></div>
<h2 class="abs section-title" style="top:2518px">Free Estimate/Contact Us</h2>
<div class="abs field" style="left:112px;top:2581px;width:237px">Name*</div>
<div class="abs field" style="left:357px;top:2581px;width:239px">Email*</div>
<div class="abs field" style="left:604px;top:2581px;width:239px">City*</div>
<div class="abs field" style="left:851px;top:2581px;width:237px">Square footage*</div>
<div class="abs field" style="left:112px;top:2640px;width:237px">Property Type*</div>
<div class="abs field" style="left:357px;top:2640px;width:239px">Type of Cleaning*</div>
<div class="abs field" style="left:604px;top:2640px;width:239px">Freqency*</div>
<div class="abs field" style="left:851px;top:2640px;width:237px">dd-mm-yy</div>
<div class="abs submit">SUBMIT</div>

<!-- Vendors -->
<h2 class="abs section-title" style="top:2952px">Preferred Vendors</h2>
<div class="abs vendor" style="left:140px"><span></span></div>
<div class="abs vendor" style="left:384px"><span></span></div>
<div class="abs vendor" style="left:628px"><span></span></div>
<div class="abs vendor" style="left:872px"><span></span></div>

<!-- Testimonial -->
<div class="abs testimonial" role="img" aria-label="Gloved hands wiping a white table with a spray bottle near potted flowers"></div>
<blockquote class="abs quote">“Lorem ipsum dolor sit amet, consectetur adipiscing elit, sed do eiusmod tempor incididunt ut labore et dolore magna aliqua. Ut enim ad minim veniam, quis nostrud exercitation ullamco laboris nisi ut aliquip ex ea commodo consequat. Duis aute irure dolor in reprehenderit in voluptate velit esse cillum dolore”<cite>- John Doe, Company name</cite></blockquote>
<div class="abs slide-btn" style="left:112px;background:#fff"><svg width="14" height="14" viewBox="0 0 14 14"><path d="M9 2 4 7l5 5" fill="none" stroke="#333" stroke-width="2"/></svg></div>
<div class="abs slide-btn" style="left:173px;background:var(--blue)"><svg width="14" height="14" viewBox="0 0 14 14"><path d="M5 2l5 5-5 5" fill="none" stroke="#fff" stroke-width="2"/></svg></div>

<!-- Footer -->
<footer class="abs footer"></footer>
<span class="abs social" style="left:112px" aria-label="Social link"></span>
<span class="abs social" style="left:155px" aria-label="Social link"></span>
<span class="abs social" style="left:198px" aria-label="Social link"></span>
<p class="abs copyright">© Copyrights 2020 All Rights Reserved | Shorepoint Studio</p>

</body>
</html>
```